Creative, fresh business card design for Ripplecraft Facades

We need a fresh, creative business card design for Ripplecraft Facades. We are the manufacturer of Ripplecraft Facades in Australia. Wall panels are 2400 x 1200mm panels made from MDF and feature Ripplecraft patterns on the face of the panel. The colours to be used are green, silver/grey and white RGB
Red 187
Green 207
Blue 65.

An idea is to possibly use a watermark of one of our designs as a background (like on the "Grids" design on the left hand side of page 2 of our brochure).

Target Market(s)

Interior designers, architects, builders and home renovators

Industry/Entity Type

Business

Contact Information for Business Card

Details to go on the card are:
Our logo (attached),
Slogan: "Decorative panels for interiors and exteriors",
Contact name,
Position,
Mobile phone number,
Business address,
Business phone,
Business fax,
Website and
Email address.

I have attached a few images of our panels and our brochure for reference.

The colours of the business card should feature our logo colours which are: RGB
Red 187
Green 207
Blue 65

Requirements
Must have
• Very modern fonts and design. Some of the designs shown especially the "Prisms" design which is a popular design.
Nice to have
• Creative but simple design. Very contemporary.
Should not have
• Anything ornate or old fashioned.

```html
<!DOCTYPE html>
<html lang="en">
<head>
<meta charset="utf-8">
<title>Ripplecraft Facades – Business Card</title>
<link rel="stylesheet" href="https://fonts.googleapis.com/css2?family=Arimo:wght@400;700&family=Open+Sans:wght@400;600&display=swap">
<style>
  :root {
    --brand-green: #bbcf41;
    --band-silver: #a9aaad;
    --card-dark: #2c2d2f;
    --card-dark-deep: #1f2021;
    --ink-dark: #1d1e1f;
    --text-white: #ffffff;
    --stage: #3b3b3c;
  }
  html, body {
    margin: 0;
    width: 1200px;
    height: 1000px;
    overflow: hidden;
    background: var(--stage);
  }
  .business-card {
    position: absolute;
    left: 355px;
    top: 70px;
    width: 490px;
    height: 860px;
    overflow: hidden;
    background: linear-gradient(160deg, var(--card-dark) 0%, var(--card-dark-deep) 100%);
    box-shadow: 0 18px 40px rgba(0,0,0,0.45);
  }
  .brand-block {
    position: absolute;
    left: 0; top: 0;
    width: 100%;
    height: 250px;
    background: var(--brand-green);
  }
  .brand-name {
    position: absolute;
    left: 22px;
    top: 78px;
    margin: 0;
    font-family: "Arimo", sans-serif;
    font-weight: 700;
    font-size: 74px;
    letter-spacing: -3px;
    color: var(--ink-dark);
    line-height: 1;
  }
  .name-band {
    position: absolute;
    left: 0; top: 250px;
    width: 100%;
    height: 68px;
    background: var(--band-silver);
  }
  .company-name {
    position: absolute;
    right: 22px;
    top: 12px;
    margin: 0;
    font-family: "Arimo", sans-serif;
    font-weight: 400;
    font-size: 40px;
    letter-spacing: -1px;
    color: var(--text-white);
    line-height: 1;
  }
  .slogan {
    position: absolute;
    left: 30px;
    top: 338px;
    margin: 0;
    font-family: "Open Sans", sans-serif;
    font-size: 17px;
    letter-spacing: 8px;
    line-height: 30px;
    color: var(--brand-green);
  }
  .contact-block {
    position: absolute;
    left: 120px;
    top: 490px;
    font-family: "Open Sans", sans-serif;
    color: var(--text-white);
  }
  .person-name {
    margin: 0;
    font-family: "Arimo", sans-serif;
    font-weight: 700;
    font-size: 34px;
    color: var(--brand-green);
    line-height: 1.1;
  }
  .person-role {
    margin: 4px 0 22px;
    font-size: 20px;
  }
  .address {
    margin: 0 0 22px;
    font-size: 18px;
    line-height: 24px;
    font-style: normal;
  }
  .contact-list {
    list-style: none;
    margin: 0;
    padding: 0;
    font-size: 18px;
    line-height: 29px;
  }
  .contact-list li {
    display: flex;
    align-items: center;
    gap: 12px;
  }
  .contact-icon {
    width: 16px;
    height: 16px;
    fill: var(--brand-green);
    flex: none;
  }
  .accent { color: var(--brand-green); }
</style>
</head>
<body>
  <article class="business-card">
    <header class="brand-block">
      <p class="brand-name">Ripplecraft</p>
    </header>
    <div class="name-band">
      <p class="company-name">Ripplecraft Facades</p>
    </div>
    <p class="slogan">Decorative Panels for<br>interiors and exteriors</p>

    <section class="contact-block">
      <h1 class="person-name">Dario Lenz</h1>
      <p class="person-role">Director</p>
      <address class="address">Your Street Address,<br>New York, 1234</address>
      <ul class="contact-list">
        <li>
          <svg class="contact-icon" viewBox="0 0 16 16" aria-hidden="true"><path d="M4 0h8a1 1 0 0 1 1 1v14a1 1 0 0 1-1 1H4a1 1 0 0 1-1-1V1a1 1 0 0 1 1-1zm.5 2v10h7V2zM8 13a1 1 0 1 0 0 2 1 1 0 0 0 0-2z"/></svg>
          +000 123 456 789
        </li>
        <li>
          <svg class="contact-icon" viewBox="0 0 16 16" aria-hidden="true"><path d="M3.5 1 6 4 4.6 5.8a9 9 0 0 0 5.6 5.6L12 10l3 2.5-1.5 2.5C7 15 1 9 1 2.5z"/></svg>
          +000 123 456 789
        </li>
        <li>
          <svg class="contact-icon" viewBox="0 0 16 16" aria-hidden="true"><path d="M4 1h7v4H4zM1 6h14v8H1zm3 2v2h2V8zm4 0v2h4V8z"/></svg>
          +000 123 456 789
        </li>
        <li>
          <svg class="contact-icon" viewBox="0 0 16 16" aria-hidden="true"><path d="M1 3h14v10H1zm1 1 6 5 6-5z"/></svg>
          yourname@email.com
        </li>
        <li>
          <svg class="contact-icon" viewBox="0 0 16 16" aria-hidden="true"><path d="M10 1a5 5 0 1 1-3.2 8.8L2.4 14.2 1 12.8l4.4-4.4A5 5 0 0 1 10 1zm0 2a3 3 0 1 0 0 6 3 3 0 0 0 0-6z"/></svg>
          www.<span class="accent">websitename</span>.com
        </li>
      </ul>
    </section>
  </article>
</body>
</html>
```